Corvane Holdings , new business card design

investment firm with corporate clients . need double sided business card , vertical and horizontal options ,logo must be clear. prefer pantone colors only and sharp design. website also www.corvane.ae

Khalid Bin Tarrafi
Managing Director
Tel. +971 4 387 2940
Mobile +971 50 518 2403
khalid@corvane.ae
Q-Span Plaza, officw 18-B07, Warqa Gardens, Dubai

Contact Information for Business Card

Khalid Bin Tarrafi
Managing Director

Font styles to use
Serif

Colors

Designer to choose colors to be used in the design.

```html
<!DOCTYPE html>
<html lang="en">
<head>
<meta charset="utf-8">
<title>Corvane Holdings – Business Card</title>
<link href="https://fonts.googleapis.com/css2?family=Roboto:wght@400;500&family=Roboto+Condensed:wght@700&display=swap" rel="stylesheet">
<style>
  :root {
    --backdrop: #2b2b2d;
    --card-white: #f1f1f1;
    --brand-blue: #366899;
    --name-blue: #3f6c9b;
    --ink: #111418;
    --text-grey: #4a4a4a;
    --white: #ffffff;
  }
  html, body {
    margin: 0;
    padding: 0;
    width: 1200px;
    height: 960px;
    overflow: hidden;
    background: var(--backdrop);
  }
  .canvas {
    position: relative;
    width: 1200px;
    height: 960px;
  }
  .card {
    position: absolute;
    width: 600px;
    height: 343px;
    box-shadow: 0 3px 6px rgba(0,0,0,0.45);
  }
  .card--front {
    left: 314px;
    top: 113px;
    background: var(--card-white);
  }
  .card--back {
    left: 311px;
    top: 472px;
    background: var(--brand-blue);
  }
  .edge-bar {
    position: absolute;
    left: 0;
    width: 11px;
  }
  .edge-bar--accent { top: 48px; height: 42px; background: var(--brand-blue); }
  .edge-bar--dark-1 { top: 109px; height: 34px; background: var(--ink); }
  .edge-bar--dark-2 { top: 162px; height: 75px; background: var(--ink); }

  .holder-name {
    position: absolute;
    left: 41px;
    top: 48px;
    margin: 0;
    font-family: "Roboto Condensed", sans-serif;
    font-weight: 700;
    font-size: 20px;
    color: var(--name-blue);
    letter-spacing: 0.1px;
  }
  .holder-title {
    position: absolute;
    left: 41px;
    top: 73px;
    margin: 0;
    font-family: "Roboto", sans-serif;
    font-weight: 500;
    font-size: 15px;
    color: var(--ink);
  }
  .office-address {
    position: absolute;
    left: 41px;
    top: 107px;
    margin: 0;
    font-family: "Roboto", sans-serif;
    font-style: normal;
    font-size: 14px;
    line-height: 18px;
    color: var(--text-grey);
  }
  .contact-list {
    position: absolute;
    left: 41px;
    top: 161px;
    margin: 0;
    padding: 0;
    list-style: none;
    font-family: "Roboto", sans-serif;
    font-size: 14px;
    line-height: 19px;
    color: var(--text-grey);
  }
  .contact-list li {
    display: flex;
    align-items: center;
    gap: 7px;
  }
  .contact-icon {
    width: 13px;
    height: 13px;
    fill: var(--name-blue);
  }
  .wordmark {
    position: absolute;
    font-family: "Roboto", sans-serif;
    font-weight: 400;
    text-transform: uppercase;
    white-space: nowrap;
  }
  .wordmark--front {
    right: 58px;
    top: 262px;
    font-size: 21px;
    letter-spacing: 4px;
    color: var(--ink);
  }
  .wordmark--back {
    right: 43px;
    top: 240px;
    font-size: 21px;
    letter-spacing: 4px;
    color: var(--white);
  }
  .back-website {
    position: absolute;
    right: 42px;
    top: 284px;
    font-family: "Roboto", sans-serif;
    font-weight: 500;
    font-size: 16px;
    letter-spacing: 5.2px;
    color: var(--white);
  }
</style>
</head>
<body>
<main class="canvas">

  <section class="card card--front" aria-label="Business card front">
    <span class="edge-bar edge-bar--accent"></span>
    <span class="edge-bar edge-bar--dark-1"></span>
    <span class="edge-bar edge-bar--dark-2"></span>

    <h1 class="holder-name">KHALID BIN TARRAFI</h1>
    <p class="holder-title">MANAGING DIRECTOR</p>

    <address class="office-address">Q-Span Plaza, officw 18-B07<br>Warqa Gardens, Dubai</address>

    <ul class="contact-list">
      <li>
        <svg class="contact-icon" viewBox="0 0 24 24" aria-hidden="true"><path d="M6.6 10.8a15.1 15.1 0 0 0 6.6 6.6l2.2-2.2c.3-.3.7-.4 1-.2 1.1.4 2.3.6 3.6.6.6 0 1 .4 1 1V20c0 .6-.4 1-1 1C10.6 21 3 13.4 3 4c0-.6.4-1 1-1h3.5c.6 0 1 .4 1 1 0 1.3.2 2.5.6 3.6.1.3 0 .7-.2 1z"/></svg>
        <span>+971 4 387 2940</span>
      </li>
      <li>
        <svg class="contact-icon" viewBox="0 0 24 24" aria-hidden="true"><path d="M7 1h10a2 2 0 0 1 2 2v18a2 2 0 0 1-2 2H7a2 2 0 0 1-2-2V3a2 2 0 0 1 2-2zm0 3v14h10V4zm5 15.5a1.2 1.2 0 1 0 0 2.4 1.2 1.2 0 0 0 0-2.4z"/></svg>
        <span>+971 50 518 2403</span>
      </li>
      <li>
        <svg class="contact-icon" viewBox="0 0 24 24" aria-hidden="true"><path d="M2 5h20v14H2zm2 2v.4l8 5 8-5V7zm0 2.8V17h16V9.8l-8 5z"/></svg>
        <span>khalid@corvane.ae</span>
      </li>
      <li>
        <svg class="contact-icon" viewBox="0 0 24 24" aria-hidden="true"><path d="M12 2a10 10 0 1 0 0 20 10 10 0 0 0 0-20zm-1 17.9A8 8 0 0 1 4.2 10L9 14.8v1a2 2 0 0 0 2 2zm6.9-2.5a2 2 0 0 0-1.9-1.4h-1v-3a1 1 0 0 0-1-1H8v-2h2a1 1 0 0 0 1-1V7h2a2 2 0 0 0 2-2v-.4a8 8 0 0 1 2.9 12.8z"/></svg>
        <span>www.corvane.ae</span>
      </li>
    </ul>

    <div class="wordmark wordmark--front">Corvane Holdings</div>
  </section>

  <section class="card card--back" aria-label="Business card back">
    <div class="wordmark wordmark--back">Corvane Holdings</div>
    <div class="back-website">www.corvane.ae</div>
  </section>

</main>
</body>
</html>
```